Tolvik Commercial Cleaning is lookong for a new business card design.

A fresh new design that's professional and stylish. We need a serious upgrade to our business cards. I have included pictures of our existing ones. Our clients include professional individuals and business owners. We woupdblike something professional and upbeat. Please have fun and see what you come uo with.

Target Market(s)

Property managers, business owners, facility managers and other similar professionals

Industry/Entity Type

Janitorial

Contact Information for Business Card

Name, cell, office number, email, web address

Font styles to use
Sans Serif

Colors

Designer to choose colors to be used in the design.

Requirements
Must have
• please use the green color in our logo
Nice to have
• Bar code
Should not have
• Address

```html
<!DOCTYPE html>
<html lang="en">
<head>
<meta charset="utf-8">
<title>Tolvik Commercial Cleaning – Business Card</title>
<link href="https://fonts.googleapis.com/css2?family=Fredoka:wght@500;600&family=Arimo:wght@400&family=Quicksand:wght@500&display=swap" rel="stylesheet">
<style>
  :root {
    --brand-green: #2ea94a;
    --brand-green-dark: #1f7f35;
    --brand-green-light: #45c864;
    --card-white: #f8f8f6;
    --ink-grey: #5d5d5d;
    --rule-grey: #8a8a8a;
    --backdrop: #1c1c1c;
    --paper-white: #ffffff;
  }
  * { margin: 0; padding: 0; box-sizing: border-box; }
  html, body { width: 1200px; height: 963px; overflow: hidden; }
  body {
    background: var(--backdrop);
    display: flex;
    flex-direction: column;
    align-items: center;
    justify-content: center;
    gap: 60px;
    font-family: "Arimo", Arial, sans-serif;
  }
  .card {
    width: 640px;
    height: 366px;
    border-radius: 28px;
    position: relative;
    overflow: hidden;
  }
  .card-front {
    background: var(--card-white);
    display: flex;
    align-items: center;
    padding: 0 44px 0 56px;
  }
  .brand-block {
    width: 240px;
    font-family: "Fredoka", sans-serif;
    font-weight: 600;
    color: var(--brand-green);
    font-size: 32px;
    line-height: 1.08;
    letter-spacing: 0.5px;
  }
  .divider {
    width: 1.5px;
    height: 160px;
    background: var(--rule-grey);
    margin: 0 30px 0 14px;
  }
  .contact-block { flex: 1; min-width: 0; }
  .person-name {
    font-family: "Fredoka", sans-serif;
    font-weight: 600;
    font-size: 32px;
    color: var(--brand-green);
    margin-bottom: 18px;
    letter-spacing: 0.5px;
    white-space: nowrap;
  }
  .contact-list { list-style: none; }
  .contact-item {
    display: flex;
    align-items: center;
    gap: 10px;
    font-size: 17px;
    color: var(--ink-grey);
    line-height: 1.75;
    white-space: nowrap;
  }
  .contact-icon { width: 16px; height: 16px; flex-shrink: 0; }

  .card-back {
    background: linear-gradient(135deg, var(--brand-green-light) 0%, var(--brand-green) 45%, var(--brand-green-dark) 100%);
  }
  .back-footer {
    position: absolute;
    left: 40px;
    right: 40px;
    bottom: 34px;
    display: flex;
    justify-content: space-between;
    align-items: baseline;
    color: var(--paper-white);
    white-space: nowrap;
  }
  .back-name {
    font-family: "Fredoka", sans-serif;
    font-weight: 600;
    font-size: 22px;
  }
  .back-tagline {
    font-family: "Quicksand", sans-serif;
    font-weight: 500;
    font-style: italic;
    font-size: 20px;
  }
</style>
</head>
<body>

  <section class="card card-front" aria-label="Business card front">
    <div class="brand-block">tolvik<br>commercial<br>cleaning</div>
    <div class="divider"></div>
    <div class="contact-block">
      <p class="person-name">marin castell</p>
      <ul class="contact-list">
        <li class="contact-item">
          <svg class="contact-icon" viewBox="0 0 24 24" aria-hidden="true"><path fill="var(--brand-green)" d="M6.6 10.8a15.5 15.5 0 0 0 6.6 6.6l2.2-2.2a1 1 0 0 1 1-.25 11.4 11.4 0 0 0 3.6.57 1 1 0 0 1 1 1V20a1 1 0 0 1-1 1A17 17 0 0 1 3 4a1 1 0 0 1 1-1h3.5a1 1 0 0 1 1 1c0 1.25.2 2.45.57 3.6a1 1 0 0 1-.25 1z"/></svg>
          (555) 014-2087
        </li>
        <li class="contact-item">
          <svg class="contact-icon" viewBox="0 0 24 24" aria-hidden="true"><rect x="2.5" y="5" width="19" height="14" rx="1.5" fill="none" stroke="var(--brand-green)" stroke-width="2"/><path d="M3 6l9 7 9-7" fill="none" stroke="var(--brand-green)" stroke-width="2"/></svg>
          marin@tolvikcleaning.com
        </li>
        <li class="contact-item">
          <svg class="contact-icon" viewBox="0 0 24 24" aria-hidden="true"><g fill="none" stroke="var(--brand-green)" stroke-width="2"><circle cx="12" cy="12" r="9.5"/><ellipse cx="12" cy="12" rx="4" ry="9.5"/><path d="M2.5 12h19M4 7h16M4 17h16"/></g></svg>
          www.tolvikcleaning.com
        </li>
      </ul>
    </div>
  </section>

  <section class="card card-back" aria-label="Business card back">
    <div class="back-footer">
      <span class="back-name">tolvik commercial cleaning</span>
      <span class="back-tagline">spotless spaces, every visit</span>
    </div>
  </section>

</body>
</html>
```